Request for Business Card Design

Hi. My name is Marlene, I am looking for a new business card design for my company, Quarrow Signal Instruments, LLC. I really like the design you did for Tarsel Venture and was hoping you could do something similar using our full logo and our mark. I am also open to any raised texture design using our mark. I have attached our full logo, which would need to be somewhere on the card, as well as the mark in both outline and full form, as well as our brand colors / guide. The card does not have to be white, as long as our logo and mark appear. I actually like darker colored business cards more, but am open to all options. If you are interested in working with me, please let me know. We would also take the business card design into letterhead design if you can do that.

```html
<!DOCTYPE html>
<html lang="en">
<head>
<meta charset="utf-8">
<title>Quarrow Signal Instruments – Business Card</title>
<link href="https://fonts.googleapis.com/css2?family=Open+Sans:wght@400;600;700;800&display=swap" rel="stylesheet">
<style>
  :root {
    --stage: #2b2d30;
    --card-dark: #3a3a3c;
    --brand-blue: #1597c4;
    --brand-blue-deep: #0f7fa8;
    --brand-blue-light: #27aede;
    --ink-white: #ffffff;
    --ink-soft: #e6e6e6;
  }
  * { box-sizing: border-box; margin: 0; padding: 0; }
  html, body {
    width: 1200px; height: 780px; overflow: hidden;
    background: var(--stage);
    font-family: "Open Sans", Arial, sans-serif;
  }
  .canvas {
    position: relative; width: 1200px; height: 780px;
    display: flex; align-items: center; justify-content: center; gap: 50px;
  }
  .card {
    position: relative; width: 540px; height: 309px;
    overflow: hidden; border-radius: 3px;
    box-shadow: 0 14px 34px rgba(0,0,0,.45);
  }

  /* Front */
  .card-front { background: var(--card-dark); color: var(--ink-white); }
  .card-front .swoosh { position: absolute; inset: 0; width: 100%; height: 100%; }
  .brand {
    position: absolute; top: 40px; right: 40px;
    display: flex; align-items: center; gap: 12px;
  }
  .brand-dot {
    width: 40px; height: 40px; border-radius: 50%;
    background: var(--brand-blue);
  }
  .brand-name {
    font-weight: 800; font-size: 19px; letter-spacing: 1.5px;
    text-transform: uppercase; color: var(--ink-white); line-height: 1.15;
    width: 200px;
  }
  .person {
    position: absolute; top: 128px; left: 120px; text-align: right; width: 150px;
  }
  .person-name {
    font-weight: 700; font-size: 34px; color: var(--brand-blue); line-height: 1;
  }
  .person-title { font-size: 15px; color: var(--ink-white); margin-top: 4px; }
  .divider {
    position: absolute; top: 122px; left: 292px;
    width: 1.5px; height: 88px; background: var(--ink-soft);
  }
  .contacts {
    position: absolute; top: 124px; left: 306px;
    list-style: none; font-size: 13.5px; line-height: 21px;
  }
  .contacts li { display: flex; align-items: center; gap: 8px; white-space: nowrap; }
  .contacts svg { width: 13px; height: 13px; flex: none; }
  .address {
    position: absolute; left: 26px; bottom: 14px;
    font-size: 15px; color: var(--ink-white); letter-spacing: .2px;
  }

  /* Back */
  .card-back {
    background: linear-gradient(120deg, var(--brand-blue-deep) 0%, var(--brand-blue) 55%, var(--brand-blue-light) 100%);
  }
  .texture {
    position: absolute; inset: 0;
    background: linear-gradient(100deg, rgba(0,90,120,.25) 0%, rgba(0,90,120,.1) 50%, rgba(255,255,255,.18) 100%);
  }
  .back-brand {
    position: absolute; left: 40px; bottom: 36px;
    display: flex; align-items: center; gap: 8px;
  }
  .back-brand .brand-dot { width: 22px; height: 22px; background: var(--ink-white); }
  .back-brand .brand-name { font-size: 11px; width: auto; letter-spacing: 1px; }
</style>
</head>
<body>
<main class="canvas">

  <section class="card card-front" aria-label="Business card front">
    <svg class="swoosh" viewBox="0 0 540 309" preserveAspectRatio="none" aria-hidden="true">
      <path d="M0 192 C 120 212, 200 262, 300 265 C 400 268, 480 246, 540 232 L 540 309 L 0 309 Z" fill="var(--brand-blue)"/>
      <path d="M36 176 C 130 212, 200 250, 300 254 C 390 257, 450 240, 495 228" fill="none" stroke="var(--ink-white)" stroke-width="3.5" stroke-linecap="round"/>
    </svg>

    <div class="brand">
      <span class="brand-dot"></span>
      <span class="brand-name">Quarrow Signal Instruments</span>
    </div>

    <div class="person">
      <p class="person-name">Marlene</p>
      <p class="person-title">Director</p>
    </div>
    <span class="divider"></span>

    <ul class="contacts">
      <li>
        <svg viewBox="0 0 16 16"><path d="M4 1l3 3-2 2c1 2 3 4 5 5l2-2 3 3-2 3C7 15 1 9 1 3z" fill="var(--brand-blue)"/></svg>
        +001 555 210 4836
      </li>
      <li>
        <svg viewBox="0 0 16 16"><rect x="3" y="1" width="10" height="5" fill="none" stroke="var(--brand-blue)" stroke-width="1.5"/><rect x="1" y="6" width="14" height="8" rx="1" fill="var(--brand-blue)"/></svg>
        +001 555 210 7719
      </li>
      <li>
        <svg viewBox="0 0 16 16"><circle cx="8" cy="8" r="6.5" fill="none" stroke="var(--brand-blue)" stroke-width="1.5"/><path d="M1.5 8h13M8 1.5c-3 3-3 10 0 13M8 1.5c3 3 3 10 0 13" fill="none" stroke="var(--brand-blue)" stroke-width="1.2"/></svg>
        www.quarrowsignal.com
      </li>
      <li>
        <svg viewBox="0 0 16 16"><rect x="1" y="3" width="14" height="10" rx="1" fill="var(--brand-blue)"/><path d="M1.5 3.5L8 9l6.5-5.5" fill="none" stroke="var(--card-dark)" stroke-width="1.2"/></svg>
        info@quarrowsignal.com
      </li>
    </ul>

    <p class="address">1180 Meridian Park Way • Fairlow, CO 80999</p>
  </section>

  <section class="card card-back" aria-label="Business card back">
    <div class="texture" role="img" aria-label="Raised repeating brand-mark texture in tonal blue"></div>
    <div class="back-brand">
      <span class="brand-dot"></span>
      <span class="brand-name">Quarrow Signal Instruments</span>
    </div>
  </section>

</main>
</body>
</html>
```